New Business Cards for Tormin Group

We need a new Business Card to compliment our new logo. We are a vibrant design, manufacture and install business providing recreation areas, public parks and Municipal spaces. We want business cards that are classy, modern and clean.

We have recently changed our logo, and are celebrating our 40th anniversary. We want business cards with a new modern design to reflect our status.

Target Market(s)

Customers

Contact Information for Business Card

We need all the details of our 3 offices as per the business card attached. Please disregard the old logo on the business card, the other three files show our new logo.

Requirements
Must have
• All info as per attached business card but with new logo.
Nice to have

```html
<!DOCTYPE html>
<html lang="en">
<head>
<meta charset="utf-8">
<title>Tormin Group – Business Card</title>
<link rel="stylesheet" href="https://fonts.googleapis.com/css2?family=Barlow:wght@400;600&display=swap">
<style>
  :root {
    --page-bg: #e9e7e7;
    --card-bg: #ffffff;
    --map-tint: #fbeeee;
    --brand-red: #e1262d;
    --text-grey: #4a4a4a;
    --band: #574b4e;
    --band-text: #ffffff;
  }
  * { margin: 0; padding: 0; box-sizing: border-box; }
  html, body {
    width: 1200px; height: 800px; overflow: hidden;
    background: var(--page-bg);
    font-family: "Barlow", Arial, sans-serif;
    color: var(--text-grey);
  }
  .card {
    position: absolute; left: 80px; top: 106px;
    width: 1040px; height: 588px;
    background: var(--card-bg);
    box-shadow: 0 10px 30px rgba(0,0,0,0.18);
    overflow: hidden;
  }
  .card__map {
    position: absolute; inset: 0 0 74px 0;
    background: linear-gradient(120deg, #fdf6f6 0%, var(--map-tint) 45%, #fdf3f3 100%);
  }
  .contact-person { position: absolute; left: 60px; top: 68px; }
  .contact-person__name {
    font-size: 37px; font-weight: 600; color: var(--brand-red); line-height: 1.1;
  }
  .contact-person__role { font-size: 22px; margin-top: 4px; letter-spacing: 0.3px; }
  .contact-person__list { list-style: none; margin-top: 18px; font-size: 21px; }
  .contact-person__list li { display: flex; align-items: center; gap: 12px; height: 30px; letter-spacing: 0.3px; }
  .contact-person__list svg { width: 18px; height: 20px; flex: none; }

  .brand {
    position: absolute; left: 640px; top: 118px;
    display: flex; align-items: center; gap: 18px;
  }
  .brand__dot { width: 64px; height: 64px; border-radius: 50%; background: var(--brand-red); }
  .brand__name {
    font-size: 50px; font-weight: 600; color: var(--brand-red);
    letter-spacing: 1px; line-height: 1;
  }

  .office { position: absolute; top: 308px; font-size: 22px; line-height: 31px; letter-spacing: 0.3px; }
  .office--head { left: 56px; }
  .office--dubai { left: 406px; }
  .office--qatar { left: 741px; }
  .office__title { font-size: 23px; font-weight: 600; color: var(--brand-red); margin-bottom: 8px; }

  .divider { position: absolute; top: 326px; width: 1.5px; height: 142px; background: var(--brand-red); }
  .divider--one { left: 349px; }
  .divider--two { left: 686px; }

  .web-band {
    position: absolute; left: 0; right: 0; top: 514px; height: 47px;
    background: var(--band); color: var(--band-text);
    display: flex; align-items: center; justify-content: center;
    font-size: 21px; letter-spacing: 6px;
  }
</style>
</head>
<body>
  <main class="card">
    <div class="card__map" role="img" aria-label="Faint pale red world map spread across the card background"></div>

    <section class="contact-person">
      <h1 class="contact-person__name">Rami Haddad</h1>
      <p class="contact-person__role">Managing Partner</p>
      <ul class="contact-person__list">
        <li>
          <svg viewBox="0 0 20 20" aria-hidden="true"><path fill="#e1262d" d="M4 1l4 4-2 3c1 2 3 4 5 5l3-2 4 4-3 3C9 18 2 11 1 4z"/></svg>
          +971 (0)50 555 0142
        </li>
        <li>
          <svg viewBox="0 0 20 20" aria-hidden="true"><rect x="4" y="1" width="12" height="18" rx="2" fill="none" stroke="#e1262d" stroke-width="2"/><rect x="8" y="15" width="4" height="1.6" fill="#e1262d"/></svg>
          rami@tormingroup.com
        </li>
      </ul>
    </section>

    <div class="brand">
      <span class="brand__dot" aria-hidden="true"></span>
      <span class="brand__name">TORMIN GROUP</span>
    </div>

    <section class="office office--head">
      <h2 class="office__title">Head office</h2>
      <p>40112 Abu Dhabi, U.A.E</p>
      <p>P. +971 (0)2 5550184</p>
      <p>F. +971 (0)2 5550185</p>
      <p>sales@tormingroup.com</p>
    </section>
    <span class="divider divider--one"></span>
    <section class="office office--dubai">
      <h2 class="office__title">Dubai Office</h2>
      <p>208845 Dubai, U.A.E.</p>
      <p>P. +971 (0)4 5550127</p>
      <p>F. +971(0)4 5550128</p>
      <p>sales@tormingroup.com</p>
    </section>
    <span class="divider divider--two"></span>
    <section class="office office--qatar">
      <h2 class="office__title">Qatar Office</h2>
      <p>17320 Doha, Qatar</p>
      <p>P.+974 55500931</p>
      <p>F. +974 55500932</p>
      <p>sales@tormingroup.com</p>
    </section>

    <footer class="web-band">www.tormingroup.com</footer>
  </main>
</body>
</html>
```